Varentoria Business Card and Letter Head

We are a leadership assessment consultancy based in Sydney, Australia. We help executive-level decison-makers select leaders for more senior level roles in corporate and government organisations. Our methodology is based on the latest research from the field of neuroscience.
We need a business card design and matching letter head that presents our company, Varentoria, as a:
1. trusted adviser to senior executive-level decison makers
2. niche consultancy who are experts in the field of assessing leadership talent
3. results-focused solution provider who balance scientific methods with pragmatic solutions
The following company details should be used in all designs:
Company Name: Varentoria
Details (for business card):
Derek Hanford
Prime Capacity Officer
Level 29, Marlow Tower
7 Marlow Square
Sydney, NSW 2000 Australia
Phone: 1300 582 714
Mobile: 0412 637 258
Email: derek.hanford@varentoria-example.com.au
Website: varentoria-example.com.au
I have attached the logo for Varentoria (for both a white and black background) - your business card and letter head designs must incoporate this logo and colour scheme.
Thanks for your interest in this project, I'm looking forward to receiving your ideas.
Regards,
Derek
Target Market(s)
Executive-level decison-makers in corporate and government organisations (e.g., CEO, VP, Head of Human Resources)
Industry/Entity Type
Leadership
Look and feel

```html
<!DOCTYPE html>
<html lang="en">
<head>
<meta charset="utf-8">
<title>Varentoria Business Card</title>
<link href="https://fonts.googleapis.com/css2?family=Open+Sans:wght@400;700&family=Arimo:wght@400;700&display=swap" rel="stylesheet">
<style>
  :root {
    --backdrop: #ecebe8;
    --card: #ffffff;
    --ink: #3c3c3c;
    --ink-soft: #555555;
    --accent: #c0281c;
    --accent-faint: #f6ddd5;
    --frame: #8a8a8a;
  }
  * { margin: 0; padding: 0; box-sizing: border-box; }
  html, body {
    width: 1200px; height: 665px; overflow: hidden;
    background: var(--backdrop);
  }
  .canvas { position: relative; width: 1200px; height: 665px; }
  .card {
    position: absolute; top: 168px;
    width: 540px; height: 310px;
    background: var(--card);
    box-shadow: 0 2px 10px rgba(0,0,0,0.12);
    overflow: hidden;
  }
  .card--front { left: 40px; }
  .card--back { left: 620px; }
  .card__sweep { position: absolute; inset: 0; width: 100%; height: 100%; }

  .wordmark {
    position: absolute;
    display: flex; align-items: center; gap: 9px;
    font-family: "Open Sans", sans-serif; font-weight: 700;
    color: var(--ink); letter-spacing: -0.5px; line-height: 1;
  }
  .wordmark__square { background: var(--accent); flex: none; }
  .card--front .wordmark { left: 36px; top: 62px; font-size: 28px; }
  .card--front .wordmark__square { width: 20px; height: 20px; }
  .card--back .wordmark { left: 50px; top: 138px; font-size: 54px; }
  .card--back .wordmark__square { width: 34px; height: 34px; }

  .contact {
    position: absolute; right: 26px; top: 40px;
    padding: 8px 12px 10px 0;
    border-right: 4px solid var(--frame);
    border-bottom: 4px solid var(--frame);
    font-family: Arimo, sans-serif; font-size: 12.5px; line-height: 19px;
    color: var(--ink); text-align: right;
  }
  .contact__row { display: flex; justify-content: flex-end; align-items: center; gap: 6px; }
  .contact__icon { width: 12px; height: 12px; flex: none; }
  .contact__address { padding-right: 18px; margin-bottom: 4px; }

  .person {
    position: absolute; left: 40px; bottom: 52px;
    font-family: "Open Sans", sans-serif;
  }
  .person__name { color: var(--accent); font-weight: 700; font-size: 15px; }
  .person__title { color: var(--ink-soft); font-size: 12.5px; margin-top: 4px; }

  .web {
    position: absolute; right: 40px; bottom: 40px;
    font-family: Arimo, sans-serif; font-size: 14px; color: var(--ink);
  }
  .web__name { color: var(--accent); font-weight: 700; }
</style>
</head>
<body>
<main class="canvas">

  <section class="card card--front" aria-label="Business card front">
    <svg class="card__sweep" viewBox="0 0 540 310" aria-hidden="true">
      <line x1="250" y1="300" x2="470" y2="-10" stroke="var(--accent-faint)" stroke-width="6"/>
    </svg>

    <div class="wordmark"><span class="wordmark__square"></span>Varentoria</div>

    <div class="contact">
      <div class="contact__address">Level 29, Marlow Tower,<br>7 Marlow Square, Sydney,<br>NSW 2000 Australia</div>
      <div class="contact__row">1300 582 714
        <svg class="contact__icon" viewBox="0 0 12 12"><circle cx="6" cy="6" r="6" fill="var(--accent)"/><path d="M4 3 L5.5 3 L5.8 5 L5 5.6 Q5.6 7 6.8 7.2 L7.4 6.4 L9 6.8 L9 8.4 Q5 9 3.4 4 Z" fill="#fff"/></svg>
      </div>
      <div class="contact__row">0412 637 258
        <svg class="contact__icon" viewBox="0 0 12 12"><circle cx="6" cy="6" r="6" fill="var(--accent)"/><rect x="4" y="2.5" width="4" height="7" rx="0.8" fill="#fff"/></svg>
      </div>
      <div class="contact__row">derek.hanford@varentoria-example.com.au
        <svg class="contact__icon" viewBox="0 0 12 12"><circle cx="6" cy="6" r="6" fill="var(--accent)"/><rect x="3" y="4" width="6" height="4.2" fill="#fff"/><path d="M3 4 L6 6.4 L9 4" stroke="var(--accent)" stroke-width="0.7" fill="none"/></svg>
      </div>
      <div class="contact__row">www.varentoria-example.com.au
        <svg class="contact__icon" viewBox="0 0 12 12"><circle cx="6" cy="6" r="6" fill="var(--accent)"/><path d="M1 6 H11 M6 1 Q3 6 6 11 M6 1 Q9 6 6 11" stroke="#fff" stroke-width="0.8" fill="none"/></svg>
      </div>
    </div>

    <div class="person">
      <div class="person__name">Derek Hanford</div>
      <div class="person__title">Prime Capacity Officer</div>
    </div>
  </section>

  <section class="card card--back" aria-label="Business card back">
    <svg class="card__sweep" viewBox="0 0 540 310" aria-hidden="true">
      <line x1="220" y1="320" x2="520" y2="40" stroke="var(--accent-faint)" stroke-width="6"/>
    </svg>

    <div class="wordmark"><span class="wordmark__square"></span>Varentoria</div>

    <div class="web">www.<span class="web__name">varentoria-example</span>.com.au</div>
  </section>

</main>
</body>
</html>
```